Envelope Design - Winner can do follow-up business

- Varnoko.com is a Swiss-based online store selling business shirts and accessories for business men
- Please visit the webpage to make yourself familiar with the company. Although the text is in German, with Plimbo translator you should be able to understand the main content.
- Our clients are mainly business men between 30 and 60 years old. Mostly with a high income working in the service industry (banking, insurance, lawyers, etc.). Sometimes there wives purchase the shirts for them ;-)
- The colors and the logo are given, as they are also used for the print materials (please see files in attachment)
- I am running several businesses and often need a talented web designer --> the winner gets substantial follow-up business
your task:
-for our company we need a new envelope design
-It should be simple and modern
-please use one of the logos in the followings.
-suprise me :)

```html
<!DOCTYPE html>
<html lang="en">
<head>
<meta charset="utf-8">
<title>Varnoko Envelope Set</title>
<link href="https://fonts.googleapis.com/css2?family=Open+Sans:wght@400;600&display=swap" rel="stylesheet">
<style>
  :root {
    --brand-red: #ee3a2c;
    --brand-gold: #e5d462;
    --paper: #ffffff;
    --edge: #6f6f6f;
    --backdrop: #dcd7d1;
    --ink: #1d1d1d;
  }
  * { margin: 0; padding: 0; box-sizing: border-box; }
  html, body {
    width: 1200px;
    height: 953px;
    overflow: hidden;
    background: var(--backdrop);
    font-family: "Open Sans", sans-serif;
  }
  .stationery {
    position: relative;
    width: 1200px;
    height: 953px;
  }
  .envelope {
    position: absolute;
    background: var(--paper);
    border: 1px solid var(--edge);
  }
  .envelope--back  { left: 135px; top: 41px;  width: 1003px; height: 460px; }
  .envelope--flap  { left: 40px;  top: 218px; width: 1005px; height: 473px; }
  .envelope--front { left: 151px; top: 427px; width: 1004px; height: 474px; }

  .flap-line {
    position: absolute;
    left: 0; top: 0;
    width: 100%;
    height: 160px;
  }
  .flap-line path { fill: none; stroke: var(--edge); stroke-width: 1; vector-effect: non-scaling-stroke; }

  .wordmark {
    position: absolute;
    font-weight: 600;
    line-height: 1;
    white-space: nowrap;
  }
  .wordmark--red-centered {
    left: 0; right: 0; top: 44px;
    text-align: center;
    color: var(--brand-red);
    font-size: 48px;
    letter-spacing: 6px;
  }
  .brand-lockup--centered {
    position: absolute;
    left: 0; right: 0; top: 36px;
    display: flex;
    flex-direction: column;
    align-items: center;
    gap: 14px;
  }
  .brand-lockup--centered .wordmark {
    position: static;
    color: var(--brand-gold);
    font-size: 32px;
    letter-spacing: 4px;
  }
  .brand-square {
    background: var(--brand-red);
  }
  .brand-lockup--centered .brand-square { width: 34px; height: 34px; }

  .brand-lockup--left {
    position: absolute;
    left: 28px; top: 18px;
    width: 286px;
    display: flex;
    flex-direction: column;
    align-items: center;
    gap: 22px;
  }
  .brand-lockup--left .brand-square { width: 56px; height: 56px; }
  .brand-lockup--left .wordmark {
    position: static;
    color: var(--brand-gold);
    font-size: 50px;
    letter-spacing: 6px;
  }

  .contact-line {
    position: absolute;
    display: flex;
    align-items: center;
    gap: 12px;
    top: 418px;
    font-size: 20px;
    color: var(--ink);
  }
  .contact-line--address { left: 28px; }
  .contact-line--web { right: 28px; }
  .contact-line svg { display: block; }

  .footer-band {
    position: absolute;
    left: -1px; right: -1px; bottom: -1px;
    height: 8px;
    background: var(--brand-red);
  }
</style>
</head>
<body>
<main class="stationery">

  <section class="envelope envelope--back" aria-label="Envelope back, red wordmark">
    <svg class="flap-line" viewBox="0 0 973 160" preserveAspectRatio="none" aria-hidden="true">
      <path d="M0 0 C12 40 14 68 70 82 L455 150 Q486 156 517 150 L903 82 C959 68 961 40 973 0"/>
    </svg>
    <span class="wordmark wordmark--red-centered">VARNOKO</span>
  </section>

  <section class="envelope envelope--flap" aria-label="Envelope back, gold wordmark">
    <svg class="flap-line" viewBox="0 0 975 160" preserveAspectRatio="none" aria-hidden="true">
      <path d="M0 0 C12 40 14 68 70 82 L456 150 Q487 156 518 150 L905 82 C961 68 963 40 975 0"/>
    </svg>
    <div class="brand-lockup--centered">
      <span class="brand-square" aria-hidden="true"></span>
      <span class="wordmark">VARNOKO</span>
    </div>
  </section>

  <section class="envelope envelope--front" aria-label="Envelope front">
    <div class="brand-lockup--left">
      <span class="brand-square" aria-hidden="true"></span>
      <span class="wordmark">VARNOKO</span>
    </div>

    <p class="contact-line contact-line--address">
      <svg width="18" height="26" viewBox="0 0 18 26" aria-hidden="true">
        <path d="M9 0C4 0 0 4 0 9c0 6.5 9 17 9 17s9-10.5 9-17c0-5-4-9-9-9z" fill="var(--brand-red)"/>
        <circle cx="9" cy="9" r="3.4" fill="#fff"/>
      </svg>
      <span>Street Name, City Name, State Zipcode</span>
    </p>

    <p class="contact-line contact-line--web">
      <svg width="24" height="24" viewBox="0 0 24 24" aria-hidden="true" fill="none" stroke="var(--brand-red)" stroke-width="1.6">
        <circle cx="12" cy="12" r="10.5"/>
        <ellipse cx="12" cy="12" rx="4.5" ry="10.5"/>
        <line x1="1.5" y1="12" x2="22.5" y2="12"/>
        <path d="M3.5 6.5h17M3.5 17.5h17"/>
      </svg>
      <span>www.varnoko.com</span>
    </p>

    <div class="footer-band" aria-hidden="true"></div>
  </section>

</main>
</body>
</html>
```